Harrow Grading LLC business card design

Excavation company business cards

Contact Information for Business Card

Harrow Grading LLC cell phone 208-417-6290 office phone 208-319-4856 harrowgradingllc@maplecove.com Driveways, site prep, retaining walls, septic systems, rock delivery

Colors

Designer to choose colors to be used in the design.

```html
<!DOCTYPE html>
<html lang="en">
<head>
<meta charset="utf-8">
<title>Harrow Grading LLC — Business Card</title>
<link rel="stylesheet" href="https://fonts.googleapis.com/css2?family=Roboto:wght@300;400;700&display=swap">
<style>
  :root {
    --backdrop-light: #d4d4d4;
    --backdrop-dark: #a9a9a9;
    --brand-orange: #ec6f24;
    --brand-orange-deep: #c95a1c;
    --card-white: #ffffff;
    --ink-grey: #4a4a4a;
    --text-light: #ffffff;
    --divider: rgba(255, 255, 255, 0.55);
  }
  * { box-sizing: border-box; margin: 0; padding: 0; }
  html, body { width: 1200px; height: 788px; overflow: hidden; }
  body {
    background: linear-gradient(180deg, var(--backdrop-light), var(--backdrop-dark));
    font-family: "Roboto", Arial, sans-serif;
    position: relative;
  }
  .card {
    position: absolute;
    width: 540px;
    height: 309px;
    border-radius: 18px;
    overflow: hidden;
    box-shadow: 0 14px 30px rgba(0, 0, 0, 0.28);
  }
  .card--front { left: 40px; top: 240px; background: var(--card-white); }
  .card--back { left: 620px; top: 240px; background: var(--brand-orange); }

  /* front */
  .front-band {
    position: absolute; left: 0; right: 0; bottom: 0; height: 158px;
    background: var(--brand-orange);
  }
  .brand-lockup {
    position: absolute; left: 0; right: 0; top: 52px;
    display: flex; align-items: center; justify-content: center; gap: 10px;
  }
  .brand-mark { width: 22px; height: 22px; background: var(--brand-orange); }
  .brand-name {
    color: var(--brand-orange); font-weight: 700; font-size: 30px;
    letter-spacing: 1px; text-transform: uppercase;
  }
  .holder {
    position: absolute; left: 36px; bottom: 58px; text-align: right;
    color: var(--text-light);
  }
  .holder-name { font-weight: 700; font-size: 24px; letter-spacing: 0.5px; }
  .holder-title { font-weight: 300; font-size: 17px; margin-top: 2px; }
  .band-divider {
    position: absolute; left: 230px; bottom: 28px; width: 1px; height: 100px;
    background: var(--divider);
  }
  .contact-list {
    position: absolute; left: 250px; bottom: 30px; list-style: none;
    color: var(--text-light); font-size: 13.5px; font-weight: 400;
  }
  .contact-item { display: flex; align-items: center; gap: 8px; line-height: 23px; }
  .contact-icon { width: 12px; height: 12px; flex: none; }

  /* back */
  .back-lockup {
    position: absolute; inset: 0;
    display: flex; align-items: center; justify-content: center;
  }
  .back-name {
    color: var(--brand-orange-deep); font-weight: 700; font-size: 40px;
    letter-spacing: 1px; text-transform: uppercase;
  }
</style>
</head>
<body>
  <section class="card card--front" aria-label="Business card front">
    <div class="brand-lockup">
      <span class="brand-mark"></span>
      <span class="brand-name">Harrow Grading LLC</span>
    </div>
    <div class="front-band"></div>
    <div class="holder">
      <p class="holder-name">DALE WREN</p>
      <p class="holder-title">Founder</p>
    </div>
    <div class="band-divider"></div>
    <ul class="contact-list">
      <li class="contact-item">
        <svg class="contact-icon" viewBox="0 0 24 24" fill="#fff"><path d="M6.6 10.8a15.1 15.1 0 0 0 6.6 6.6l2.2-2.2a1 1 0 0 1 1-.25 11.4 11.4 0 0 0 3.6.57 1 1 0 0 1 1 1V20a1 1 0 0 1-1 1A17 17 0 0 1 3 4a1 1 0 0 1 1-1h3.5a1 1 0 0 1 1 1c0 1.25.2 2.45.57 3.57a1 1 0 0 1-.25 1z"/></svg>
        <span>208-319-4856</span>
      </li>
      <li class="contact-item">
        <svg class="contact-icon" viewBox="0 0 24 24" fill="none" stroke="#fff" stroke-width="2.4"><rect x="6" y="2" width="12" height="20" rx="2"/><line x1="10" y1="18" x2="14" y2="18"/></svg>
        <span>208-417-6290</span>
      </li>
      <li class="contact-item">
        <svg class="contact-icon" viewBox="0 0 24 24" fill="none" stroke="#fff" stroke-width="2.4"><rect x="2" y="5" width="20" height="14" rx="1"/><path d="M2 6l10 7 10-7"/></svg>
        <span>harrowgradingllc@maplecove.com</span>
      </li>
      <li class="contact-item">
        <svg class="contact-icon" viewBox="0 0 24 24" fill="none" stroke="#fff" stroke-width="2.2"><circle cx="12" cy="12" r="10"/><path d="M2 12h20M12 2c3 3 3 17 0 20M12 2c-3 3-3 17 0 20"/></svg>
        <span>www.harrowgradingllc.com</span>
      </li>
    </ul>
  </section>

  <section class="card card--back" aria-label="Business card back">
    <div class="back-lockup">
      <span class="back-name">Harrow Grading LLC</span>
    </div>
  </section>
</body>
</html>
```